Website Design for Gold Buying Company in Australia

We are looking for a Website layout for a company who buy gold pieces from trade and the public.

They would like to communicate that its easy, safe, a great way to make more money, and they pay the best prices in australia for Gold jewelery

Target Market(s)

Adults based in Australia aged 25-60 who are looking to make some extra money

Industry/Entity Type

It Company

Number of Pages Required

2 pages

Requirements
Must have
• Must have a homepage and a page to use for content.

• Will have a feed for the latest Gold, silver and platinum prices they are buying and selling at.

• Needs to have a from on the homepage where people can submit their details to be sent a ''Vaultpack'' which allows them to send gold pieces to eb valued and bought by the company.

Nice to have
• Would be nice to have a steped out graphic of how the ''Vaultpack by mail'' process works [Request a Kit, Send in your Gold, We Value and grade it, We pay you cash, cheque of Direct Deposit]

• Imagery will be gold related

• Colour schemes are not a major Issue-but using some gold or silver would be a good idea
Should not have
• No cheesy gold graphics please :)

```html
<!DOCTYPE html>
<html lang="en">
<head>
<meta charset="utf-8">
<title>Aureline Trading – Website Layout</title>
<link href="https://fonts.googleapis.com/css2?family=Mulish:wght@200;300;400;800&family=Arimo:wght@400;700&display=swap" rel="stylesheet">
<style>
:root{
  --gold:#9a5a14;
  --gold-text:#b07a1f;
  --gold-light:#e9d3ae;
  --link:#a3600f;
  --nav-top:#5d6266;
  --nav-bottom:#17191b;
  --cream-top:#f6ede2;
  --cream-bottom:#fcf9f5;
  --footer:#e5e5e8;
  --grey-text:#555;
  --body-text:#3a3a3a;
  --rule:#d8d2c8;
}
*{box-sizing:border-box;margin:0;padding:0}
html,body{width:1200px;height:2675px;overflow:hidden;background:#fff}
.canvas{position:relative;width:1200px;height:2675px;overflow:hidden;font-family:"Arimo",Arial,sans-serif;color:var(--body-text)}
.page{position:absolute;left:0;width:1200px;height:1340px}
.page--home{top:0}
.page--content{top:1340px}
.abs{position:absolute}
.top-rule{left:4px;right:2px;top:7px;height:3px;background:#b4b4b4;border-bottom:1px solid #e2e2e2}
.logo{left:88px;top:48px;font-family:"Mulish",sans-serif;font-weight:200;font-size:76px;line-height:1;letter-spacing:-1px;color:var(--gold-light);white-space:nowrap}
.utility{top:72px;display:flex;gap:42px;left:948px}
.utility svg{width:20px;height:20px}
.trade{left:924px;top:126px;font-family:"Mulish",sans-serif;font-size:21px;color:var(--gold-text);letter-spacing:-.5px;white-space:nowrap}
.navband{left:4px;right:2px;top:164px;height:128px;background:linear-gradient(var(--nav-top),var(--nav-bottom) 60%,#0f1011)}
.nav{left:0;top:164px;width:1200px;height:60px;font-family:"Mulish",sans-serif;font-size:21px;letter-spacing:-.5px}
.nav a{position:absolute;top:0;height:60px;line-height:60px;text-align:center;color:#fff;text-decoration:none;white-space:nowrap}
.nav a.active{background:#fff;color:var(--gold-text);border-radius:0 0 10px 10px;box-shadow:0 2px 4px rgba(0,0,0,.3)}
.nav .sep{position:absolute;top:6px;width:1px;height:50px;background:#3a3d40;border-right:1px solid #6a6e72}
.cream{left:4px;right:2px;top:602px;height:604px;background:linear-gradient(var(--cream-top),var(--cream-bottom))}
.banner{left:44px;top:237px;width:1120px;height:365px;border-radius:20px 20px 0 0;overflow:hidden;
  background:radial-gradient(ellipse at 30% 45%,#b88a3a 0%,#7a5219 35%,#4a3010 55%,transparent 70%),linear-gradient(100deg,#6d4a18 0%,#9c7840 45%,#a8875a 60%,#c9a46a 85%,#dcb678 100%)}
.banner-head{left:770px;top:338px;color:#fff;font-family:"Mulish",sans-serif;font-weight:400;line-height:1;white-space:nowrap}
.banner-head .b1{display:block;margin-left:50px;font-weight:200;font-size:86px;letter-spacing:-4px;line-height:.9}
.banner-head .b2{display:block;font-weight:800;font-size:34px;margin-top:-4px;letter-spacing:-1px;line-height:1}
.banner-head .b3{display:block;margin-left:103px;font-weight:300;font-size:56px;letter-spacing:-3px;margin-top:-10px;line-height:1}
.kit-panel{left:44px;top:602px;width:1120px;height:244px;border-radius:0 0 22px 22px;background:linear-gradient(#fff 40%,#eceef1);box-shadow:0 2px 4px rgba(0,0,0,.25);border-top:2px solid #b8c2d8}
.kit-title{left:94px;top:620px;font-family:"Mulish",sans-serif;line-height:1}
.kit-title .k1{display:block;font-size:30px;font-weight:300;color:#9b8165;letter-spacing:-1px}
.kit-title .k2{display:block;font-size:58px;font-weight:800;color:var(--gold);letter-spacing:-2px;margin:2px 0 0 -2px}
.kit-title .k3{display:block;font-size:30px;font-weight:300;color:#9b8165;margin-left:92px;letter-spacing:-1px}
.kit-note{left:96px;top:766px;width:360px;font-size:14px;line-height:20px;letter-spacing:.5px;color:#333}
.required{left:377px;top:808px;font-size:16px;color:var(--link);text-decoration:underline}
.field{position:absolute;height:34px;border:1px solid #c7c7c7;background:#fff;box-shadow:inset 1px 1px 2px rgba(0,0,0,.12);font-size:15px;color:#777;line-height:32px;padding-left:14px}
.kit-btn{left:839px;top:676px;width:299px;height:89px;border-radius:26px;border:3px solid #6d4a12;
  background:linear-gradient(#f3e3b0,#c8a04a 45%,#a47a25 55%,#d9bb6c);text-align:center;line-height:83px;
  font-family:"Mulish",sans-serif;font-weight:800;font-size:33px;color:#fff;letter-spacing:-.5px;text-shadow:0 1px 2px rgba(80,50,0,.6)}
.sec-title{font-family:"Mulish",sans-serif;font-size:33px;letter-spacing:-1.5px;line-height:1;color:var(--gold)}
.sec-title b{font-weight:800}
.sec-title span{font-weight:300;color:#8a7560}
.sec-sub{font-family:"Mulish",sans-serif;font-size:16px;color:#666;letter-spacing:-.3px;margin-top:2px}
.copy{width:490px;font-size:16px;line-height:20px;color:var(--body-text)}
.copy p{margin-bottom:26px}
.copy strong{color:var(--link);font-weight:700}
.copy a{color:var(--link)}
.more{font-size:16px;color:var(--link);text-decoration:underline}
.feed{left:633px;top:946px;width:489px;list-style:none;font-family:"Mulish",sans-serif;font-size:16.5px;color:#555}
.feed li{height:36px;line-height:34px;border-bottom:2px solid var(--rule);padding-left:8px;white-space:nowrap}
.feed .arr{color:#7c8fb5;font-size:12px;margin-right:6px}
.feed .date{color:var(--link)}
.footer{left:4px;right:2px;top:1206px;height:115px;background:var(--footer);border-top:3px solid #cfcfd3}
.foot-left{left:76px;top:1254px;font-size:14px;letter-spacing:1px;color:var(--grey-text)}
.foot-right{left:877px;top:1254px;font-size:14px;letter-spacing:1px;color:var(--grey-text)}
.foot-right a{color:var(--grey-text)}
</style>
</head>
<body>
<div class="canvas">

<!-- Homepage -->
<section class="page page--home">
  <div class="abs top-rule"></div>
  <div class="abs logo">AURELINE.COM.AU</div>
  <div class="abs utility">
    <svg viewBox="0 0 20 20"><path d="M3 10 10 4l7 6M5 9v7h10V9M8 16v-4h4v4" fill="none" stroke="#222" stroke-width="1.6"/></svg>
    <svg viewBox="0 0 20 20"><path d="M8 4h4v3H8zM3 13h4v3H3zM8 13h4v3H8zM13 13h4v3h-4zM10 7v3M5 13v-3h10v3" fill="none" stroke="#666" stroke-width="1.2"/></svg>
    <svg viewBox="0 0 20 20"><path d="M3 7h14v9H3zM3 7l7 5 7-5" fill="none" stroke="#666" stroke-width="1.2"/></svg>
  </div>
  <div class="abs trade">TRADE ENQUIRIES</div>
  <div class="abs navband"></div>
  <nav class="abs nav">
    <a class="active" style="left:73px;width:156px">ABOUT US</a>
    <a style="left:247px;width:160px">BUY &amp; SELL</a>
    <span class="sep" style="left:406px"></span>
    <a style="left:408px;width:198px">HOW IT WORKS</a>
    <span class="sep" style="left:606px"></span>
    <a style="left:608px;width:186px">QUESTIONS</a>
    <span class="sep" style="left:793px"></span>
    <a style="left:795px;width:156px">BULLION</a>
    <span class="sep" style="left:950px"></span>
    <a style="left:952px;width:182px">CONTACTS</a>
  </nav>
  <div class="abs cream"></div>
  <div class="abs banner" role="img" aria-label="Close-up photograph of gold chains, coins and jewellery with light streaks"></div>
  <h1 class="abs banner-head"><span class="b1">BEST</span><span class="b2">PRICES IN</span><span class="b3">AUSTRALIA</span></h1>

  <div class="abs kit-panel"></div>
  <h2 class="abs kit-title"><span class="k1">REQUEST YOUR</span><span class="k2">VAULTPACK</span><span class="k3">TODAY</span></h2>
  <p class="abs kit-note">Send in your Gold, We Value and grade it, We pay you cash, cheque of Direct Deposit</p>
  <span class="abs required">*Required</span>
  <div class="field" style="left:466px;top:613px;width:312px">First Name*</div>
  <div class="field" style="left:466px;top:650px;width:312px">Last Name*</div>
  <div class="field" style="left:466px;top:688px;width:342px">Address*</div>
  <div class="field" style="left:466px;top:725px;width:250px">City*</div>
  <div class="field" style="left:720px;top:725px;width:52px">Stat</div>
  <div class="field" style="left:466px;top:762px;width:100px">Zip*</div>
  <div class="field" style="left:572px;top:762px;width:200px">Phone</div>
  <div class="field" style="left:466px;top:800px;width:342px">Email*</div>
  <div class="abs kit-btn">GET YOUR KIT!</div>

  <div class="abs" style="left:83px;top:877px">
    <h3 class="sec-title"><b>WHO</b> <span>WE ARE</span></h3>
    <div class="sec-sub">COMPANY PROFILE OVERVIEW</div>
  </div>
  <div class="abs copy" style="left:81px;top:948px">
    <p><strong>Aliquam vitae lorem da.</strong><br>Integer pede nisi, adipng eget, gravida sagittis, placerat vel. Sed a us id <a href="#">nisi feugiat</a> convallis. Vivamus telluse urna, tincidunt vel, commodo sit amet, viverra vitae, enim. Donec vitae odio.</p>
    <p><strong>Vivamus telluse urna</strong>, tincidunt vel, <a href="#">commodo sit amet</a>, viverra ec vitae odio. Vivamus ut turpis. Cras arcu. tortor. Sed lesuada isse porttitor, mi id tincidunt tristique, nulla nisi feugiat libero.</p>
  </div>
  <a class="abs more" style="left:445px;top:1150px">more about us &gt;&gt;</a>

  <div class="abs" style="left:633px;top:877px">
    <h3 class="sec-title"><b>WHAT</b> <span>WE DO</span></h3>
    <div class="sec-sub">FEATURED SERVICES</div>
  </div>
  <ul class="abs feed">
    <li><span class="arr">&#8674;</span><span class="date">2007-06-10</span> / Lorem ipsum dolor sit amet consectetuer adipis</li>
    <li><span class="arr">&#8674;</span><span class="date">2007-06-12</span> / Consectetuer adipiscing elit hasellus sapien</li>
    <li><span class="arr">&#8674;</span><span class="date">2007-06-10</span> / Lorem ipsum dolor sit amet consectetuer adipi</li>
    <li><span class="arr">&#8674;</span><span class="date">2007-06-12</span> / Phasellus sapien tortor, fringilla vel, pretium</li>
    <li><span class="arr">&#8674;</span><span class="date">2007-06-12</span> / Nulla mi urna, faucibus eget, faucibus idodo</li>
  </ul>
  <a class="abs more" style="left:1008px;top:1150px">all services &gt;&gt;</a>

  <footer class="abs footer"></footer>
  <div class="abs foot-left">AURELINE TRADING 2009. All rights reserved</div>
  <div class="abs foot-right"><a href="#">Privacy Policy</a> &nbsp;and&nbsp; <a href="#">Terms of Use</a></div>
</section>

<!-- Content page -->
<section class="page page--content">
  <div class="abs top-rule"></div>
  <div class="abs logo">AURELINE.COM.AU</div>
  <div class="abs utility">
    <svg viewBox="0 0 20 20"><path d="M3 10 10 4l7 6M5 9v7h10V9M8 16v-4h4v4" fill="none" stroke="#222" stroke-width="1.6"/></svg>
    <svg viewBox="0 0 20 20"><path d="M8 4h4v3H8zM3 13h4v3H3zM8 13h4v3H8zM13 13h4v3h-4zM10 7v3M5 13v-3h10v3" fill="none" stroke="#666" stroke-width="1.2"/></svg>
    <svg viewBox="0 0 20 20"><path d="M3 7h14v9H3zM3 7l7 5 7-5" fill="none" stroke="#666" stroke-width="1.2"/></svg>
  </div>
  <div class="abs trade">TRADE ENQUIRIES</div>
  <div class="abs navband"></div>
  <nav class="abs nav">
    <a style="left:73px;width:156px">ABOUT US</a>
    <a class="active" style="left:247px;width:157px">BUY &amp; SELL</a>
    <span class="sep" style="left:406px"></span>
    <a style="left:408px;width:198px">HOW IT WORKS</a>
    <span class="sep" style="left:606px"></span>
    <a style="left:608px;width:186px">QUESTIONS</a>
    <span class="sep" style="left:793px"></span>
    <a style="left:795px;width:156px">BULLION</a>
    <span class="sep" style="left:950px"></span>
    <a style="left:952px;width:182px">CONTACTS</a>
  </nav>
  <div class="abs cream"></div>
  <div class="abs banner" role="img" aria-label="Close-up photograph of gold chains, coins and jewellery with light streaks"></div>
  <h1 class="abs banner-head"><span class="b1">BEST</span><span class="b2">PRICES IN</span><span class="b3">AUSTRALIA</span></h1>

  <div class="abs kit-panel"></div>
  <h2 class="abs kit-title"><span class="k1">REQUEST YOUR</span><span class="k2">VAULTPACK</span><span class="k3">TODAY</span></h2>
  <p class="abs kit-note">Send in your Gold, We Value and grade it, We pay you cash, cheque of Direct Deposit</p>
  <span class="abs required">*Required</span>
  <div class="field" style="left:466px;top:613px;width:312px">First Name*</div>
  <div class="field" style="left:466px;top:650px;width:312px">Last Name*</div>
  <div class="field" style="left:466px;top:688px;width:342px">Address*</div>
  <div class="field" style="left:466px;top:725px;width:250px">City*</div>
  <div class="field" style="left:720px;top:725px;width:52px">Stat</div>
  <div class="field" style="left:466px;top:762px;width:100px">Zip*</div>
  <div class="field" style="left:572px;top:762px;width:200px">Phone</div>
  <div class="field" style="left:466px;top:800px;width:342px">Email*</div>
  <div class="abs kit-btn">GET YOUR KIT!</div>

  <h3 class="abs sec-title" style="left:83px;top:877px"><b>WHAT</b> <span>WE BUY</span></h3>
  <div class="abs copy" style="left:81px;top:950px">
    <p><strong>Aliquam vitae lorem da.</strong><br>Integer pede nisi, adipng eget, gravida sagittis, placerat vel. Sed a us id <a href="#">nisi feugiat</a> convallis. Vivamus telluse urna, tincidunt vel, commodo sit amet, viverra vitae, enim. Donec vitae odio.</p>
    <p><strong>Vivamus telluse urna</strong>, tincidunt vel, <a href="#">commodo sit amet</a>, viverra ec vitae odio. Vivamus ut turpis. Cras arcu. tortor. Sed lesuada isse porttitor, mi id tincidunt tristique, nulla nisi feugiat libero.</p>
  </div>
  <div class="abs copy" style="left:657px;top:950px">
    <p><strong>Aliquam vitae lorem da.</strong><br>Integer pede nisi, adipng eget, gravida sagittis, placerat vel. Sed a us id <a href="#">nisi feugiat</a> convallis. Vivamus telluse urna, tincidunt vel, commodo sit amet, viverra vitae, enim. Donec vitae odio.</p>
    <p><strong>Vivamus telluse urna</strong>, tincidunt vel, <a href="#">commodo sit amet</a>, viverra ec vitae odio. Vivamus ut turpis. Cras arcu. tortor. Sed lesuada isse porttitor, mi id tincidunt tristique, nulla nisi feugiat libero.</p>
  </div>

  <footer class="abs footer"></footer>
  <div class="abs foot-left">AURELINE TRADING 2009. All rights reserved</div>
  <div class="abs foot-right"><a href="#">Privacy Policy</a> &nbsp;and&nbsp; <a href="#">Terms of Use</a></div>
</section>

</div>
</body>
</html>
```